Redesign This Psychology Website

We would like a slight redesign of this successful psychology (relationship counselling) website:

www.TheKelvaleClinic.com.au

We are updating the website, and we'd like a slight refresh of the design and style.

Please keep to very similar colours, and use the same logo. We're looking for around 10 page templates, however the main one is the home page.

Keep in mind, this website already converts quite well, so we want a new, fresh design in keeping with this one. Please don't bother designing something too extremely different.

thanks :)

Target Market(s)

couples who are looking for relationship counselling. Men and women, 25 - 70, across Australia

Industry/Entity Type

Psychology

Number of Pages Required

5+ page

Font styles to use
Sans Serif

Colors
87cfc6
b7a5cd
ec1f27
ffffff
cee9f5

Requirements
Must have
• a similar look to the current design, just looking for a slight refresh.
• Search bar
• Areas for lots of photos
• same logo
• lots of content areas
Nice to have
• great content areas, where we can display a lot of content and our areas.
Should not have
• no colors like orange, etc.
• should not have a totally different feel.

```html
<!DOCTYPE html>
<html lang="en">
<head>
<meta charset="utf-8">
<title>The Kelvale Clinic – Couples Counselling</title>
<link href="https://fonts.googleapis.com/css2?family=Open+Sans:wght@400;600;700&display=swap" rel="stylesheet">
<style>
:root{
  --teal:#87cfc6;
  --teal-dark:#5fb8ad;
  --teal-text:#2fa89a;
  --lilac:#b7a5cd;
  --lilac-dark:#9a86b6;
  --red:#ec1f27;
  --coral:#e05a4f;
  --sky:#cee9f5;
  --white:#ffffff;
  --ink:#333333;
  --body:#6b6b6b;
  --muted:#9a9a9a;
  --line:#e2e2e2;
  --bar:#f4f4f4;
  --footer:#f2f2f2;
}
*{box-sizing:border-box;margin:0;padding:0}
html,body{width:1200px;height:3495px;overflow:hidden}
body{font-family:"Open Sans",Arial,sans-serif;color:var(--body);background:var(--white);position:relative}
a{color:inherit;text-decoration:none}
.abs{position:absolute}

/* top bar */
.top-bar{left:0;top:0;width:1200px;height:40px;background:var(--bar);border-bottom:1px solid var(--line);font-size:13px;color:var(--muted)}
.top-bar .associate{position:absolute;left:147px;top:11px}
.top-bar .util{position:absolute;right:138px;top:0;display:flex;height:40px}
.top-bar .util a{padding:11px 10px;border-left:1px solid var(--line)}

/* header */
.site-header{left:0;top:40px;width:1200px;height:92px}
.brand{position:absolute;left:130px;top:22px;display:flex;align-items:center;gap:12px}
.brand-dot{width:48px;height:48px;border-radius:50%;background:var(--teal)}
.brand-name{font-size:26px;font-weight:600;color:var(--teal-text);line-height:1}
.search{position:absolute;left:472px;top:44px;width:356px;height:38px;border:1px solid var(--line);border-radius:3px;display:flex;align-items:center;padding-left:12px;gap:8px;font-size:12px;color:var(--muted)}
.call{position:absolute;right:130px;top:36px;text-align:right}
.call small{display:block;font-size:14px;color:var(--teal-text)}
.call strong{display:flex;align-items:center;gap:6px;font-size:24px;font-weight:600;color:var(--teal-text)}

/* nav */
.main-nav{left:0;top:132px;width:1200px;height:98px;background:linear-gradient(var(--teal),var(--teal-dark));display:flex;padding-left:130px;border-top:1px solid #a9ddd6}
.main-nav a{color:var(--white);font-size:17px;font-weight:600;text-transform:uppercase;text-align:center;line-height:1.15;display:flex;align-items:center;justify-content:center;border-right:1px solid rgba(255,255,255,.45);padding:0 14px}
.main-nav a:last-child{border-right:0}

/* hero */
.hero{left:0;top:230px;width:1200px;height:325px;background:linear-gradient(180deg,#5a4a6a 0%,#8d6c7c 45%,#c9846c 75%,#3a2a2e 100%)}
.hero h1{position:absolute;left:126px;top:170px;font-size:37px;font-weight:600;color:var(--white);letter-spacing:.5px}

/* content */
.content{left:126px;top:600px;width:600px;font-size:13.5px;line-height:1.55}
.content h2{font-size:27px;font-weight:400;color:var(--ink);line-height:1.3;margin-bottom:22px}
.content p{margin-bottom:12px}
.content h3{font-size:24px;font-weight:400;color:var(--coral);margin:44px 0 18px}
.photo{background:linear-gradient(135deg,#d7c6b6,#9f8676)}
.round{border-radius:50%;float:right;margin:0 0 10px 18px;width:265px;height:265px}
.session-photo{float:left;width:285px;height:220px;margin:0 22px 12px 10px}
.clear{clear:both}
.lead{font-weight:600;color:#555;margin-bottom:22px}
.problems{list-style:none}
.problems li{position:relative;padding-left:26px;height:33px;font-size:13.5px}
.problems li::before{content:"";position:absolute;left:4px;top:6px;border-left:7px solid var(--teal-dark);border-top:5px solid transparent;border-bottom:5px solid transparent}
.more{position:absolute;left:130px;top:2620px;width:600px}
.more .beach{position:absolute;left:0;top:0;width:265px;height:270px;border-radius:50%;background:linear-gradient(180deg,#a9d4ea,#e8d7b8)}
.more .text{position:absolute;left:288px;top:60px;width:310px;font-size:13.5px;line-height:1.55}
.more .text p{margin-bottom:10px}
.more .hl{color:var(--teal-text)}
.more .phone{color:#444}

/* sidebar */
.finder{left:765px;top:600px;width:305px;height:362px;background:var(--lilac);padding:26px 20px;color:var(--white)}
.finder h4{font-size:21px;font-weight:600;text-align:center;line-height:1.3;margin-bottom:16px}
.finder label{display:block;font-size:12px;margin:8px 0 5px}
.finder .field{height:34px;background:var(--white);border-radius:2px;font-size:11px;color:var(--muted);padding:9px 10px;display:flex;justify-content:space-between}
.finder .go{margin-top:16px;height:36px;background:var(--red);border-radius:2px;text-align:center;font-size:15px;font-weight:600;line-height:36px}
.feature{left:765px;width:305px;border:1px solid var(--line);display:flex;background:var(--white)}
.feature .copy{width:150px;flex-shrink:0;padding:22px 0 0 14px}
.feature h5{font-size:18px;font-weight:600;color:var(--ink);line-height:1.2;margin-bottom:8px}
.feature p{font-size:10px;line-height:1.45;color:var(--muted)}
.feature .btn{display:inline-block;margin-top:10px;background:var(--lilac-dark);color:var(--white);font-size:10px;padding:5px 12px}
.feature .pic{flex:1}
.mini{left:765px;width:305px;height:112px;border:1px solid var(--line);display:flex;background:var(--white)}
.mini .pic{width:150px;flex-shrink:0;height:100%}
.mini .copy{padding:16px 12px 0 14px;font-size:13px;color:var(--ink);line-height:1.3}
.mini .copy span{display:block;margin-top:6px;font-size:11px;color:var(--teal-text)}

/* footer */
.site-footer{left:0;top:3125px;width:1200px;height:285px;background:var(--footer);border-top:1px solid var(--line)}
.site-footer .brand{left:132px;top:70px}
.fcol{position:absolute;top:65px;font-size:12.5px;line-height:2.2}
.fcol h6{font-size:16px;font-weight:600;color:var(--teal-text);margin-bottom:4px;line-height:1.4}
.socials{display:flex;gap:8px;margin-top:10px}
.socials span{width:30px;height:30px;border-radius:50%;background:var(--teal-dark)}
.copyright{left:0;top:3410px;width:1200px;height:85px;border-top:1px solid var(--line);text-align:center;font-size:11px;color:var(--muted);padding-top:32px}
</style>
</head>
<body>

<div class="abs top-bar">
  <a class="associate" href="#">Join Our Associate Program →</a>
  <nav class="util"><a href="#">Home</a><a href="#">Cart</a><a href="#">Blog</a><a href="#">Resources</a><a href="#">Contact</a></nav>
</div>

<header class="abs site-header">
  <div class="brand"><span class="brand-dot"></span><span class="brand-name">The Kelvale Clinic</span></div>
  <div class="search">
    <svg width="14" height="14" viewBox="0 0 14 14"><circle cx="6" cy="6" r="4.5" fill="none" stroke="#999" stroke-width="1.5"/><line x1="9.5" y1="9.5" x2="13" y2="13" stroke="#999" stroke-width="1.5"/></svg>
    Search here
  </div>
  <div class="call">
    <small>Call Us Now</small>
    <strong><svg width="22" height="22" viewBox="0 0 24 24"><path d="M6.6 10.8a15 15 0 0 0 6.6 6.6l2.2-2.2c.3-.3.7-.4 1-.2 1.1.4 2.3.6 3.6.6.6 0 1 .4 1 1V20c0 .6-.4 1-1 1A17 17 0 0 1 3 4c0-.6.4-1 1-1h3.5c.6 0 1 .4 1 1 0 1.3.2 2.5.6 3.6.1.3 0 .7-.2 1z" fill="none" stroke="#ec1f27" stroke-width="1.8"/></svg>1300 555 014</strong>
  </div>
</header>

<nav class="abs main-nav">
  <a href="#">Counselling<br>Types</a>
  <a href="#">Relationship Counselling<br>Locations</a>
  <a href="#">Sex Therapy<br>Locations</a>
  <a href="#">About Us</a>
  <a href="#">Quizzes</a>
  <a href="#" style="width:95px">FAQ's</a>
  <a href="#">Contact</a>
</nav>

<section class="abs hero" role="img" aria-label="Couple silhouetted against a sunset sky">
  <h1>COUPLES COUNSELLING</h1>
</section>

<main class="abs content">
  <h2>We take a positive approach when helping<br>you with your relationship problems</h2>
  <div class="photo round" role="img" aria-label="Smiling couple in sunglasses, man carrying woman on his back"></div>
  <p>It can be difficult not to feel quite negative about your relationship when you are experiencing many problems with it.</p>
  <p>An important part of our couples counselling is to give each of you the opportunity to share what are the problems and issues for you in your relationship. In helping you to resolve these problems, we find it is important for our approach to be as positive as possible.</p>
  <p>We do this by focusing on a number of things:</p>
  <p style="margin-top:26px">We help you look at what dynamics you as a couple may have unwittingly fallen into, which can help take away the sense of blame that is easy to attribute entirely to your partner, so instead, the two of you can form an alliance in working on it.</p>
  <p>Additionally, quite early in the process, we have you create your positive want list based on your issues, and in doing this, we are able to work with what you are wanting that will make your relationship great for you, providing a positive repairing of your relationship.</p>
  <p>We also show you how to communicate more honestly and openly, encourage and nurture your romance, identify your love languages, make quality time together, and celebrate improvements together.</p>
  <p style="margin-top:22px">As you progress, good will and a deeper understanding between you and your partner can begin to grow, along with a mutual appreciation, and you can feel more and more in a positive spiral again.</p>
  <p style="margin-top:32px">We can show you how there is hope amidst the negativity, problems and hopelessness that it is easy to feel when you are experiencing relationship problems.</p>

  <h3>Our Session Lengths:</h3>
  <div class="photo session-photo" role="img" aria-label="Couple sitting together outdoors, one holding flowers"></div>
  <p>It is often assumed that if you have been together for a long time, that you can't expect to continue to have a satisfying relationship. Your initial session is for 50 minutes. Further sessions are available in the same 50 mins format, or alternatively you may choose, 1 and a half hours, 2 hours, or 3 hours sessions.</p>
  <p>We also have sessions available by Phone and TalkWave. After hours times are also available at select locations.</p>
  <p class="clear" style="padding-top:14px">Your initial session is for 50 minutes. Further sessions are available in the same 50 mins format, or alternatively you may choose, 1 and a half hours, 2 hours, or 3 hours sessions.</p>
  <p>We also have sessions available by Phone and TalkWave. After hours times are also available at select locations.</p>

  <h3>Common Problems We Can Help You With:</h3>
  <p class="lead">Here are some of the common problems our marriage and relationship counselling can help you with:</p>
  <ul class="problems">
    <li>We have lost that loving feeling; I don't know whether I even love my partner, or I love him but am not "in love with him" any more</li>
    <li style="margin-top:14px">We are like flatmates rather than partners, friends but not lovers anymore</li>
    <li>We argue, complain about and criticise each other</li>
    <li>One or both of us shuts down and withdraws rather than communicates well</li>
    <li>My partner is controlling or verbally abusive and I can't stand it any more</li>
    <li>My partner doesn't show me any affection</li>
    <li>We have no love life</li>
    <li>My partner won't take his/her share of the responsibilities</li>
    <li>My partner (or I) have had an affair</li>
    <li>We can't agree on finances, child rearing, or where to go on holidays</li>
    <li>My partner has to have his or her own way all the time</li>
    <li>I have problems with my in-laws, or interfering parents</li>
    <li>My partner is not supportive of me at all</li>
    <li>My partner won't listen to me</li>
    <li>I don't remember the last time we spent any quality time together, or had a Date Night</li>
    <li>We have a blended family. How do we manage stepchildren?</li>
    <li>I have no interest in sex any more</li>
    <li>Somehow I have lost myself in my relationship</li>
    <li>We can go days without talking</li>
  </ul>
</main>

<section class="more">
  <div class="beach" role="img" aria-label="Couple embracing on a beach"></div>
  <div class="text">
    <p>For more information, check our frequently asked questions about the relationship counselling process.</p>
    <p class="hl">Couples Counselling and Marriage counselling sessions are 50 mins</p>
    <p>Cost: $160 ($175 for after hours sessions or for all sessions at CBD locations)</p>
    <p>Private Health Insurance Rebates apply, and Medicare Rebates may apply.</p>
    <p class="phone">Phone 1300 555 014 to enquire or make an appointment.</p>
  </div>
</section>

<aside>
  <div class="abs finder">
    <h4>Find Our Psychologist<br>Near You</h4>
    <label>Type of Counselling</label>
    <div class="field">Select <svg width="10" height="10" viewBox="0 0 10 10"><path d="M1 3l4 4 4-4" fill="none" stroke="#999" stroke-width="1.5"/></svg></div>
    <label>Location</label>
    <div class="field"></div>
    <label>Postcode</label>
    <div class="field"></div>
    <div class="go">SEARCH</div>
  </div>

  <div class="abs feature" style="top:988px;height:172px">
    <div class="copy"><h5>Rebates<br>Available</h5><p>See which rebates apply to your sessions and claims.</p><span class="btn">Learn More</span></div>
    <div class="pic photo" role="img" aria-label="Two hands reaching toward each other at sunset" style="background:linear-gradient(135deg,#f2b35a,#6a3a2a)"></div>
  </div>
  <div class="abs feature" style="top:1248px;height:237px">
    <div class="copy"><h5>GP Referral<br>Info</h5><p>How a referral from your doctor can help you.</p><span class="btn">Learn More</span></div>
    <div class="pic photo" role="img" aria-label="Doctor in white coat with stethoscope" style="background:linear-gradient(135deg,#eef3f6,#b9c9d4)"></div>
  </div>
  <div class="abs feature" style="top:1508px;height:237px">
    <div class="copy"><h5>Anxiety and<br>Depression</h5><p>Support for anxiety and low mood, in person.</p><span class="btn">Learn More</span></div>
    <div class="pic photo" role="img" aria-label="Person sitting alone with head in hands" style="background:linear-gradient(135deg,#5a5f63,#25292c)"></div>
  </div>

  <a class="abs mini" style="top:1762px"><div class="pic photo" role="img" aria-label="Two hands touching"></div><div class="copy">What can I do if I'm living with a Narcissist?<span>Read More</span></div></a>
  <a class="abs mini" style="top:1890px"><div class="pic photo" role="img" aria-label="Woman gesturing to stay quiet"></div><div class="copy">Are You Living With a Steamroller?<span>Read More</span></div></a>
  <a class="abs mini" style="top:2016px"><div class="pic photo" role="img" aria-label="Couple sitting apart after an argument"></div><div class="copy">Did Your Relationship Start on Rocky Ground?<span>Read More</span></div></a>
  <a class="abs mini" style="top:2158px"><div class="pic photo" role="img" aria-label="Couple in a tense moment"></div><div class="copy">Why am I with a Narcissist?<span>Read More</span></div></a>
  <a class="abs mini" style="top:2286px"><div class="pic photo" role="img" aria-label="Couple talking at a table"></div><div class="copy">Letter for a Partner Doubtful About Relationship Counselling<span>Read More</span></div></a>
  <a class="abs mini" style="top:2414px"><div class="pic photo" role="img" aria-label="Couple arm wrestling"></div><div class="copy">What Are You Like In a Relationship?<span>Read More</span></div></a>
  <a class="abs mini" style="top:2542px"><div class="pic photo" role="img" aria-label="Couple looking away from each other"></div><div class="copy">How Do I Know If I'm With a Narcissist?<span>Read More</span></div></a>
  <a class="abs mini" style="top:2670px"><div class="pic photo" role="img" aria-label="Happy couple close together"></div><div class="copy">Do You Wonder Why You and Your Partner Are Together?<span>Read More</span></div></a>
  <a class="abs mini" style="top:2798px"><div class="pic photo" role="img" aria-label="Person at an office desk"></div><div class="copy">Is Your Pursuit of Success Sabotaging Your Relationships That Matter Most?<span>Read More</span></div></a>
</aside>

<footer class="abs site-footer">
  <div class="brand"><span class="brand-dot"></span><span class="brand-name">The Kelvale Clinic</span></div>
  <div class="fcol" style="left:452px"><h6>QUICK LINKS</h6>Home<br>About Us<br>Our Blogs<br>Shop Cart<br>Contact Us</div>
  <div class="fcol" style="left:620px"><h6>RESOURCES</h6>Counselling Type<br>Sex Therapy<br>Quizzes<br>FAQ<br>Relationship Counselling</div>
  <div class="fcol" style="left:823px"><h6>CONTACT US</h6>42 Harbour Lane Suite 12<br>1300 555 014<br>Email: info@kelvaleclinic.com.au
    <div class="socials"><span></span><span></span><span></span><span></span></div>
  </div>
</footer>
<div class="abs copyright">© 2017 The Kelvale Clinic. All right reserved</div>

</body>
</html>
```